Business Card Design Project

We are a construction company in Orange County, CA. We need a two sided business card. We would like the back to be our logo with web URL. Front should included Name, title, address, phone, fax and email address.

our address is
627 West Dorrance Blvd, Suite 308
Corvale, CA 92718

Our logo files are attached.

Construction

```html
<!DOCTYPE html>
<html lang="en">
<head>
<meta charset="utf-8">
<title>Korvell Business Card</title>
<link rel="stylesheet" href="https://fonts.googleapis.com/css2?family=Open+Sans:wght@400;600;700;800&display=swap">
<style>
  :root {
    --brand-blue: #1a4a7c;
    --card-white: #ffffff;
    --wave-grey: #ececec;
    --text-grey: #444444;
    --page-bg: #e8e5e1;
  }
  * { margin: 0; padding: 0; box-sizing: border-box; }
  html, body {
    width: 1200px;
    height: 1037px;
    overflow: hidden;
    background: var(--page-bg);
    font-family: "Open Sans", Arial, sans-serif;
  }
  .canvas { position: relative; width: 1200px; height: 1037px; }

  .card {
    position: absolute;
    border-radius: 26px;
    overflow: hidden;
  }

  /* Front */
  .card-front {
    left: 88px; top: 70px;
    width: 752px; height: 429px;
    background: var(--card-white);
    border: 1.5px solid #3a3a3a;
  }
  .front-stripe {
    position: absolute; right: 0; top: 0;
    width: 39px; height: 100%;
    background: var(--brand-blue);
  }
  .front-wave {
    position: absolute; left: 0; top: 0;
    width: 713px; height: 429px;
  }
  .wordmark {
    position: absolute;
    font-weight: 800;
    color: var(--brand-blue);
    letter-spacing: -2px;
    line-height: 1;
    text-align: center;
    white-space: nowrap;
  }
  .card-front .wordmark {
    left: 0; width: 713px; top: 34px;
    font-size: 92px;
  }
  .holder {
    position: absolute; left: 0; width: 713px; top: 204px;
    text-align: center;
    color: var(--brand-blue);
    font-size: 25px;
  }
  .holder-name { font-weight: 700; }
  .holder-title { font-weight: 400; }
  .contact-row {
    position: absolute; left: 0; width: 713px;
    display: flex; justify-content: center; gap: 14px;
    font-size: 18px; color: var(--text-grey);
  }
  .contact-row.row-phones { top: 304px; }
  .contact-row.row-online { top: 328px; }
  .contact-item { display: flex; align-items: center; gap: 6px; }
  .contact-item svg { width: 14px; height: 14px; fill: var(--text-grey); }
  .address {
    position: absolute; left: 0; width: 713px; top: 369px;
    text-align: center; font-size: 18px; color: var(--text-grey);
  }

  /* Back */
  .card-back {
    left: 384px; top: 549px;
    width: 734px; height: 419px;
    background: var(--brand-blue);
  }
  .card-back .wordmark {
    left: 0; width: 100%; top: 128px;
    font-size: 96px;
    color: var(--card-white);
  }
  .back-url {
    position: absolute; left: 0; width: 100%; top: 282px;
    text-align: center; color: var(--card-white);
    font-size: 18px; letter-spacing: 3.5px;
  }
</style>
</head>
<body>
<div class="canvas">

  <section class="card card-front" aria-label="Business card front">
    <svg class="front-wave" viewBox="0 0 713 429" preserveAspectRatio="none" aria-hidden="true">
      <path d="M0 334 Q356 190 713 313 L713 429 L0 429 Z" fill="var(--wave-grey)"/>
    </svg>
    <div class="front-stripe"></div>

    <div class="wordmark">KORVELL</div>

    <div class="holder">
      <span class="holder-name">Your Name,</span>
      <span class="holder-title">Title</span>
    </div>

    <div class="contact-row row-phones">
      <span class="contact-item">
        <svg viewBox="0 0 16 16" aria-label="Phone"><path d="M3.5 1.5l2.5 0 1 3.5-1.8 1.2c.8 1.8 2.2 3.2 4 4l1.2-1.8 3.5 1v2.5c0 .9-.8 1.6-1.7 1.5C6.8 13.2 2.8 9.2 2 3.2 1.9 2.3 2.6 1.5 3.5 1.5z"/></svg>
        01-234-5678
      </span>
      <span class="contact-item">
        <svg viewBox="0 0 16 16" aria-label="Fax"><path d="M4 1h6l2 2v3H4z M1 7h14v6h-2v-2H3v2H1z M4 12h8v3H4z"/></svg>
        01-234-5678
      </span>
    </div>
    <div class="contact-row row-online">
      <span class="contact-item">
        <svg viewBox="0 0 16 16" aria-label="Email"><path d="M1 3h14v10H1z M1.5 3.5L8 9l6.5-5.5" stroke="#fff" stroke-width="1.2"/></svg>
        info@korvell.com
      </span>
      <span class="contact-item">
        <svg viewBox="0 0 16 16" aria-label="Website"><circle cx="8" cy="8" r="7"/><path d="M1 8h14M8 1c-3 4-3 10 0 14M8 1c3 4 3 10 0 14" stroke="#fff" stroke-width="1" fill="none"/></svg>
        www.korvell.com
      </span>
    </div>

    <div class="address">627 West Dorrance Blvd, Suite 308, Corvale, CA&nbsp; 92718</div>
  </section>

  <section class="card card-back" aria-label="Business card back">
    <div class="wordmark">KORVELL</div>
    <div class="back-url">www.korvell.com</div>
  </section>

</div>
</body>
</html>
```